World Wide News and Current Affairs website

We intends to start up a new website which deals on New and Current Affairs.
Attention Designers,
We want a home page design for this project. Our business is based in the United States. Our goal is to become a well known brand.
The website would consist of a category for News, Business and Tech.
The theme should be beautiful and attention seeking. The website would take bulk of it's news from the US, and Europe.
Designers can get inspiration from already existing new websites such as PWJ, KLV, DASKOLM.
All designs should be clean and easy to navigate.

```html
<!DOCTYPE html>
<html lang="en">
<head>
<meta charset="utf-8">
<title>Marlow News</title>
<link href="https://fonts.googleapis.com/css2?family=Lato:wght@400;700;900&display=swap" rel="stylesheet">
<style>
:root{
  --red:#d7261e;
  --ink:#1d1d1d;
  --muted:#555;
  --topbar:#222;
  --band:#ececec;
  --gallery:#333;
  --footer:#2b2b2b;
  --line:#e3e3e3;
  --white:#fff;
}
*{box-sizing:border-box;margin:0;padding:0}
html,body{width:1200px;height:3854px;overflow:hidden}
body{font-family:'Lato',Arial,sans-serif;color:var(--ink);background:var(--white);position:relative}
a{color:inherit;text-decoration:none}
.wrap{width:1026px;margin:0 auto;position:relative}

/* top bar */
.topbar{height:58px;background:var(--topbar);color:var(--white)}
.topbar .wrap{height:58px;display:flex;align-items:center;justify-content:space-between}
.signin{border:1px solid #666;border-radius:3px;font-size:11px;font-weight:700;padding:6px 12px;display:flex;align-items:center;gap:6px;letter-spacing:.5px}
.follow{display:flex;align-items:center;gap:16px;font-size:13px;font-weight:700;letter-spacing:1px}
.follow .dot{width:11px;height:11px;border-radius:50%;background:#cfcfcf;display:inline-block}

/* header */
.header{height:84px;border-bottom:1px solid var(--line)}
.header .wrap{height:84px;display:flex;align-items:center;justify-content:space-between}
.brand{font-size:27px;font-weight:900;color:var(--red);letter-spacing:-.3px}
.nav{display:flex;gap:20px;font-size:12px;font-weight:700;align-items:center}
.nav span.caret::after{content:" \2304";font-size:10px}

/* trending */
.trending{height:70px}
.trending .wrap{height:70px;display:flex;align-items:center}
.trend-label{background:var(--red);color:var(--white);font-size:13px;font-weight:700;padding:12px 20px;letter-spacing:1px}
.trend-text{font-size:15px;color:var(--muted);margin-left:22px;flex:1}
.arrows{display:flex;gap:10px}
.arrows span{width:34px;height:34px;border-radius:50%;background:#e4e4e4;display:flex;align-items:center;justify-content:center}

/* hero */
.hero{position:absolute;top:213px;left:0;width:1200px;height:456px}
.tile{position:absolute;overflow:hidden;color:var(--white)}
.tile .cap{position:absolute;left:36px;bottom:28px;right:30px}
.date{font-size:11px;opacity:.9}
.headline{font-weight:700;line-height:1.55;margin-top:8px}
.tag{font-size:11px;font-weight:700;margin-top:10px;border-left:2px solid var(--white);padding-left:6px}

/* sections */
.section-title{font-size:24px;font-weight:700;border-left:4px solid var(--red);padding-left:14px;line-height:1}
.grid4{display:grid;grid-template-columns:repeat(4,245px);gap:15px;margin-top:42px}
.card .thumb{height:226px;position:relative}
.card .thumb .d{position:absolute;left:16px;bottom:14px;color:var(--white);font-size:10px}
.card .thumb .ic{position:absolute;right:14px;bottom:10px;width:24px;height:24px;border-radius:50%;background:var(--white);display:flex;align-items:center;justify-content:center}
.card h3{font-size:12px;font-weight:700;margin-top:16px}
.card p{font-size:11px;line-height:1.6;color:var(--muted);margin-top:6px}

.business{position:absolute;top:724px;left:0;width:1200px}
.tech{position:absolute;top:1124px;left:0;width:1200px}
.featured{position:absolute;top:1516px;left:0;width:1200px;height:822px;background:var(--band);padding-top:62px}
.video-main{height:412px;margin-top:30px;position:relative;color:var(--white);background:radial-gradient(circle at 62% 55%,#ff7a2a 0%,#b8402a 12%,#3a3f6a 35%,#1d2340 75%)}
.video-main .cap{position:absolute;left:50px;bottom:40px}
.play{position:absolute;left:455px;top:185px}
.grid3{display:grid;grid-template-columns:repeat(3,326px);gap:24px;margin-top:22px}
.mini{height:206px;position:relative;color:var(--white)}
.mini .cap{position:absolute;left:20px;bottom:14px;right:20px}
.mini .headline{font-size:12px;margin-top:4px}
.mini .tag{margin-top:4px;font-size:9px}

.affairs{position:absolute;top:2394px;left:0;width:1200px}
.gallery{position:absolute;top:2806px;left:0;width:1200px;height:388px;background:var(--gallery)}
.gallery .section-title{color:var(--white);margin-top:52px}
.gallery-row{position:absolute;top:106px;left:0;display:grid;grid-template-columns:repeat(5,240px);height:224px}

.signup{position:absolute;top:3194px;left:0;width:1200px;height:275px;overflow:hidden}
.signup .section-title{position:absolute;left:513px;top:60px}
.signup .sub{position:absolute;left:0;width:1200px;text-align:center;top:110px;font-size:15px;color:var(--muted)}
.form{position:absolute;left:352px;top:166px;display:flex}
.form .field{width:368px;height:44px;border:1px solid #ddd;font-size:12px;color:#aaa;padding:14px 30px}
.form .btn{width:124px;height:44px;background:var(--red);color:var(--white);font-weight:700;font-size:16px;display:flex;align-items:center;justify-content:center;margin-left:8px}
.device{position:absolute;left:936px;top:56px;width:170px;height:240px;border:2px solid #ccc;border-radius:22px;background:#fafafa;padding:20px 8px}
.device .screen{height:100%;background:linear-gradient(#d7261e 0 8%,#fff 8% 12%,#b9b4ad 12% 45%,#fff 45% 52%,#c8c3bd 52%)}

/* footer */
.footer{position:absolute;top:3469px;left:0;width:1200px;height:385px;background:var(--footer);color:var(--white)}
.cols{display:grid;grid-template-columns:repeat(5,1fr);padding-top:54px}
.cols h4{font-size:16px;font-weight:700;padding-bottom:10px;border-bottom:1px solid #4a4a4a;width:150px}
.cols li{list-style:none;font-size:11px;color:#cfcfcf;margin-top:9px}
.cols li::before{content:"> "}
.legal{position:absolute;top:292px;left:0;width:1200px;text-align:center;font-size:11px;color:#bdbdbd}
.legal span{padding:0 7px;border-left:1px solid #666}
.legal span:first-child{border-left:0}
.copy{position:absolute;top:336px;left:0;width:1200px;text-align:center;font-size:11px;color:#999}
.legal-rule{position:absolute;top:262px;left:87px;width:1026px;height:1px;background:#444}
</style>
</head>
<body>

<div class="topbar"><div class="wrap">
  <div class="signin"><svg width="10" height="10" viewBox="0 0 10 10"><circle cx="5" cy="3" r="2.2" fill="#fff"/><path d="M1 10c0-3 8-3 8 0z" fill="#fff"/></svg>SIGNIN</div>
  <div class="follow">FOLLOW US: <span class="dot"></span><span class="dot"></span><span class="dot"></span><span class="dot"></span><span class="dot"></span><span class="dot"></span><span class="dot"></span></div>
</div></div>

<div class="header"><div class="wrap">
  <div class="brand">Marlow News</div>
  <nav class="nav">
    <a>HOME</a><span class="caret">WORLD</span><span class="caret">BUSINESS</span><span class="caret">POLITICS</span><span class="caret">SPORTS</span><span class="caret">HEALTH</span><span class="caret">SCIENCE</span><span class="caret">TECH</span>
    <svg width="13" height="13" viewBox="0 0 13 13"><circle cx="5.5" cy="5.5" r="4" fill="none" stroke="#d7261e" stroke-width="2"/><path d="M8.5 8.5l3.5 3.5" stroke="#d7261e" stroke-width="2"/></svg>
  </nav>
</div></div>

<div class="trending"><div class="wrap">
  <div class="trend-label">TRENDING</div>
  <div class="trend-text">Lorem Ipsum is simply dummy text of the printing and typesetting industry.</div>
  <div class="arrows">
    <span><svg width="8" height="10" viewBox="0 0 8 10"><path d="M6 1L2 5l4 4" fill="none" stroke="#555" stroke-width="2"/></svg></span>
    <span><svg width="8" height="10" viewBox="0 0 8 10"><path d="M2 1l4 4-4 4" fill="none" stroke="#555" stroke-width="2"/></svg></span>
  </div>
</div></div>

<section class="hero">
  <div class="tile" style="left:0;top:0;width:661px;height:456px;background:linear-gradient(135deg,#8a6a55,#c9b29c 45%,#6e5a4c)" role="img" aria-label="Photo of colleagues talking around an office table">
    <div class="cap"><div class="date">April 15, 2017</div><div class="headline" style="font-size:20px">Lorem Ipsum is simply dummy text of the printing<br>and typesetting industry. Lorem Ipsum</div><div class="tag">TECH</div></div>
  </div>
  <div class="tile" style="left:670px;top:0;width:530px;height:226px;background:linear-gradient(135deg,#5a5550,#9c948a 50%,#3e3a36)" role="img" aria-label="Photo of hands working on documents at a desk">
    <div class="cap"><div class="date">April 15, 2017</div><div class="headline" style="font-size:15px">Lorem Ipsum is simply dummy text of the printing and<br>typesetting industry. Lorem Ipsum</div><div class="tag">TECH</div></div>
  </div>
  <div class="tile" style="left:670px;top:232px;width:530px;height:224px;background:linear-gradient(160deg,#6d7e8c,#2f3e4a 60%,#1d2830)" role="img" aria-label="Photo of a man in silhouette facing a city skyline">
    <div class="cap"><div class="date">April 15, 2017</div><div class="headline" style="font-size:15px">Lorem Ipsum is simply dummy text of the printing and<br>typesetting industry. Lorem Ipsum</div><div class="tag">TECH</div></div>
  </div>
</section>

<section class="business"><div class="wrap">
  <h2 class="section-title">Business</h2>
  <div class="grid4">
    <article class="card"><div class="thumb" style="background:linear-gradient(160deg,#a8603c,#3c4a66 60%,#1e2535)" role="img" aria-label="Photo of a speaker facing a conference audience"><span class="d">April 15, 2017</span><span class="ic"><svg width="10" height="8" viewBox="0 0 10 8"><rect x="0" y="1" width="10" height="7" fill="#333"/></svg></span></div><h3>Lorem Ipsum is simply dummy text of the</h3><p>when an unknown printer took a galley of type and scrambled it to make a type specimen</p></article>
    <article class="card"><div class="thumb" style="background:linear-gradient(160deg,#dfe4ea,#a9b4c0 60%,#6e7a86)" role="img" aria-label="Photo of a smiling woman at a laptop"><span class="d">April 15, 2017</span><span class="ic"><svg width="10" height="8" viewBox="0 0 10 8"><rect x="0" y="1" width="10" height="7" fill="#333"/></svg></span></div><h3>Lorem Ipsum is simply dummy text of the</h3><p>when an unknown printer took a galley of type and scrambled it to make a type specimen</p></article>
    <article class="card"><div class="thumb" style="background:linear-gradient(160deg,#5fc4dc,#3aa6c4)" role="img" aria-label="Illustration of a businessman with a telescope"><span class="d">April 15, 2017</span><span class="ic"><svg width="10" height="8" viewBox="0 0 10 8"><rect x="0" y="1" width="7" height="6" fill="#333"/><path d="M7 3l3-2v6L7 5z" fill="#333"/></svg></span></div><h3>Lorem Ipsum is simply dummy text of the</h3><p>when an unknown printer took a galley of type and scrambled it to make a type specimen</p></article>
    <article class="card"><div class="thumb" style="background:linear-gradient(160deg,#eceef2,#c9ccd4 60%,#4a4e5a)" role="img" aria-label="Photo of a businesswoman with glasses"><span class="d">April 15, 2017</span><span class="ic"><svg width="10" height="8" viewBox="0 0 10 8"><rect x="0" y="1" width="7" height="6" fill="#333"/><path d="M7 3l3-2v6L7 5z" fill="#333"/></svg></span></div><h3>Lorem Ipsum is simply dummy text of the</h3><p>when an unknown printer took a galley of type and scrambled it to make a type specimen</p></article>
  </div>
</div></section>

<section class="tech"><div class="wrap">
  <h2 class="section-title">Tech</h2>
  <div class="grid4">
    <article class="card"><div class="thumb" style="background:linear-gradient(160deg,#c8ccd0,#8a9096 60%,#3d4248)" role="img" aria-label="Photo of people working on laptops from above"><span class="d">April 15, 2017</span><span class="ic"><svg width="10" height="8" viewBox="0 0 10 8"><rect x="0" y="1" width="7" height="6" fill="#333"/><path d="M7 3l3-2v6L7 5z" fill="#333"/></svg></span></div><h3>Lorem Ipsum is simply dummy text of the</h3><p>when an unknown printer took a galley of type and scrambled it to make a type specimen</p></article>
    <article class="card"><div class="thumb" style="background:linear-gradient(160deg,#f2f2f2,#d2d2d2 55%,#2a2a2a)" role="img" aria-label="Photo of charts and papers on a desk"><span class="d">April 15, 2017</span><span class="ic"><svg width="10" height="8" viewBox="0 0 10 8"><rect x="0" y="1" width="10" height="7" fill="#333"/></svg></span></div><h3>Lorem Ipsum is simply dummy text of the</h3><p>when an unknown printer took a galley of type and scrambled it to make a type specimen</p></article>
    <article class="card"><div class="thumb" style="background:linear-gradient(160deg,#5a5e62,#2c2f33 60%,#15171a)" role="img" aria-label="Photo of a man in front of a chalkboard of diagrams"><span class="d">April 15, 2017</span><span class="ic"><svg width="10" height="8" viewBox="0 0 10 8"><rect x="0" y="1" width="10" height="7" fill="#333"/></svg></span></div><h3>Lorem Ipsum is simply dummy text of the</h3><p>when an unknown printer took a galley of type and scrambled it to make a type specimen</p></article>
    <article class="card"><div class="thumb" style="background:linear-gradient(160deg,#6c7580,#3b4450 55%,#7ab045)" role="img" aria-label="Photo of hands joining puzzle pieces"><span class="d">April 15, 2017</span><span class="ic"><svg width="10" height="8" viewBox="0 0 10 8"><rect x="0" y="1" width="10" height="7" fill="#333"/></svg></span></div><h3>Lorem Ipsum is simply dummy text of the</h3><p>when an unknown printer took a galley of type and scrambled it to make a type specimen</p></article>
  </div>
</div></section>

<section class="featured"><div class="wrap">
  <h2 class="section-title">Featured video</h2>
  <div class="video-main" role="img" aria-label="Video still of glowing circuit and technology icons">
    <svg class="play" width="60" height="64" viewBox="0 0 60 64"><path d="M0 0l60 32L0 64z" fill="#d7261e"/></svg>
    <div class="cap"><div class="date">April 15, 2017</div><div class="headline" style="font-size:19px">Lorem Ipsum is simply dummy text of the printing and typesetting industry.</div><div class="tag">TECH</div></div>
  </div>
  <div class="grid3">
    <div class="mini" style="background:linear-gradient(160deg,#c89a5a,#8a6a4a 55%,#4a5a6a)" role="img" aria-label="Photo of a team's hands over a desk"><div class="cap"><div class="date">April 15, 2017</div><div class="headline">Lorem Ipsum is simply dummy text of the</div><div class="tag">TECH</div></div></div>
    <div class="mini" style="background:linear-gradient(160deg,#b8b8b8,#7a7a7a 55%,#3a3a3a)" role="img" aria-label="Photo of a laptop showing charts"><div class="cap"><div class="date">April 15, 2017</div><div class="headline">Lorem Ipsum is simply dummy text of the</div><div class="tag">TECH</div></div></div>
    <div class="mini" style="background:linear-gradient(160deg,#a8702a,#4a3a40 55%,#1e2232)" role="img" aria-label="Photo of a speaker at a conference"><div class="cap"><div class="date">April 15, 2017</div><div class="headline">Lorem Ipsum is simply dummy text of the</div><div class="tag">TECH</div></div></div>
  </div>
</div></section>

<section class="affairs"><div class="wrap">
  <h2 class="section-title">Current Affairs</h2>
  <div class="grid4">
    <article class="card"><div class="thumb" style="background:linear-gradient(160deg,#e6e8ec,#b4bcc6 60%,#6a7a8a)" role="img" aria-label="Photo of a smiling young woman"><span class="d">April 15, 2017</span><span class="ic"><svg width="10" height="8" viewBox="0 0 10 8"><rect x="0" y="1" width="10" height="7" fill="#333"/></svg></span></div><h3>Lorem Ipsum is simply dummy text of the</h3><p>when an unknown printer took a galley of type and scrambled it to make a type specimen</p></article>
    <article class="card"><div class="thumb" style="background:linear-gradient(160deg,#d8d2c8,#a88866 55%,#6a5040)" role="img" aria-label="Photo of a man with glasses in an office"><span class="d">April 15, 2017</span><span class="ic"><svg width="10" height="8" viewBox="0 0 10 8"><rect x="0" y="1" width="10" height="7" fill="#333"/></svg></span></div><h3>Lorem Ipsum is simply dummy text of the</h3><p>when an unknown printer took a galley of type and scrambled it to make a type specimen</p></article>
    <article class="card"><div class="thumb" style="background:linear-gradient(160deg,#3a4450,#6a9ab8 50%,#2a2e34)" role="img" aria-label="Photo of a tablet with floating app icons"><span class="d">April 15, 2017</span><span class="ic"><svg width="10" height="8" viewBox="0 0 10 8"><rect x="0" y="1" width="10" height="7" fill="#333"/></svg></span></div><h3>Lorem Ipsum is simply dummy text of the</h3><p>when an unknown printer took a galley of type and scrambled it to make a type specimen</p></article>
    <article class="card"><div class="thumb" style="background:linear-gradient(160deg,#eaf0f4,#9ab4c8 55%,#2a3a4a)" role="img" aria-label="Photo of a person wearing a virtual reality headset"><span class="d">April 15, 2017</span><span class="ic"><svg width="10" height="8" viewBox="0 0 10 8"><rect x="0" y="1" width="10" height="7" fill="#333"/></svg></span></div><h3>Lorem Ipsum is simply dummy text of the</h3><p>when an unknown printer took a galley of type and scrambled it to make a type specimen</p></article>
  </div>
</div></section>

<section class="gallery">
  <div class="wrap"><h2 class="section-title">Photo Stream</h2></div>
  <div class="gallery-row">
    <div style="background:radial-gradient(circle,#f0c040,#b06a10 40%,#1a1208)" role="img" aria-label="Digital art of a glowing head"></div>
    <div style="background:linear-gradient(160deg,#c8c4bc,#7a7268 55%,#3a3632)" role="img" aria-label="Photo of a meeting table from above"></div>
    <div style="background:linear-gradient(160deg,#d8dce0,#8a96a2 55%,#4a5460)" role="img" aria-label="Photo of a woman touching a digital screen"></div>
    <div style="background:radial-gradient(circle at 60% 45%,#c8d8f0,#3a5a8a 30%,#0e1828)" role="img" aria-label="Photo of a hand reaching toward light"></div>
    <div style="background:radial-gradient(circle,#40c0e0,#1a5a9a 40%,#081830)" role="img" aria-label="Digital art of a glowing data ring"></div>
  </div>
</section>

<section class="signup">
  <h2 class="section-title">Stay Updated</h2>
  <p class="sub">Get the recent popular stories straight into your inbox</p>
  <div class="form"><div class="field">Email</div><div class="btn">SIGN UP</div></div>
  <div class="device" role="img" aria-label="Phone showing the mobile site"><div class="screen"></div></div>
</section>

<footer class="footer">
  <div class="wrap cols">
    <div><h4>WORLD</h4><ul><li>BUSINESS</li><li>POLITICS</li><li>SPORTS</li><li>HEALTH</li><li>SCIENCE</li><li>TECH</li></ul></div>
    <div><h4>BUSINESS</h4><ul><li>BUSINESS</li><li>POLITICS</li><li>SPORTS</li><li>HEALTH</li><li>SCIENCE</li><li>TECH</li></ul></div>
    <div><h4>POLITICS</h4><ul><li>BUSINESS</li><li>POLITICS</li><li>SPORTS</li><li>HEALTH</li><li>SCIENCE</li><li>TECH</li></ul></div>
    <div><h4>SPORTS</h4><ul><li>BUSINESS</li><li>POLITICS</li><li>SPORTS</li><li>HEALTH</li><li>SCIENCE</li><li>TECH</li></ul></div>
    <div><h4>TECH</h4><ul><li>BUSINESS</li><li>POLITICS</li><li>SPORTS</li><li>HEALTH</li><li>SCIENCE</li><li>TECH</li></ul></div>
  </div>
  <div class="legal-rule"></div>
  <div class="legal"><span>Desktop Site</span><span>Terms of Use</span><span>About</span><span>Privacy Policy</span><span>Cookies</span><span>Accessibility Help</span><span>Parental Guidance</span><span>Contact Us</span><span>Advertise with us</span><span>Ad choice</span></div>
  <div class="copy">© 2017 Marlow News, Inc. All Rights Reserved.</div>
</footer>

</body>
</html>
```